Healthcare and Professional IT Services Company need a redesigned business card

We are a IT Services company that targets small medical practices and professional business such as Attorneys, Accounts, Architects etc. We want to communicate a professional yet friendly image using recent logo redesign here on ArtHarbor. Like to see the colors blue and orange in the design. Must use the Tall Pine Computing as displayed in the new logo - then also want to incorporate the fish logo as well.

Target Market(s)

Small medical and professional services

Industry/Entity Type

It Company

Contact Information for Business Card

The usual stuff, place for name address phone website. Also maybe our tagline which is "Rooted in technology"

Requirements
Must have
• My new logo and the fish somewhere on the card

```html
<!DOCTYPE html>
<html lang="en">
<head>
<meta charset="utf-8">
<title>Tall Pine Computing – Business Card</title>
<link rel="stylesheet" href="https://fonts.googleapis.com/css2?family=Quicksand:wght@400;500;600&display=swap">
<style>
  :root {
    --bg: #ecebe9;
    --card: #ffffff;
    --blue: #1a8fd6;
    --blue-soft: #d6ebf8;
    --orange: #f5961e;
    --grey: #7c7c7c;
    --ink: #555555;
  }
  * { box-sizing: border-box; margin: 0; padding: 0; }
  html, body {
    width: 1200px; height: 997px; overflow: hidden;
    background: var(--bg);
    font-family: "Quicksand", "Century Gothic", sans-serif;
  }
  .sheet {
    position: relative; width: 1200px; height: 997px;
    display: flex; flex-direction: column; align-items: center; justify-content: center; gap: 40px;
  }
  .card {
    position: relative; width: 700px; height: 400px;
    background: var(--card); overflow: hidden;
    box-shadow: 0 6px 18px rgba(0,0,0,0.12);
  }
  /* Front */
  .card--front {
    display: flex; flex-direction: column; align-items: center; justify-content: center;
  }
  .brand {
    display: flex; align-items: center; gap: 14px;
  }
  .brand__dot {
    width: 34px; height: 34px; border-radius: 50%; background: var(--blue);
  }
  .brand__name {
    font-size: 44px; font-weight: 600; color: var(--blue); letter-spacing: -0.5px;
  }
  .tagline {
    margin-top: 34px; font-size: 20px; color: var(--grey); letter-spacing: 1.5px;
  }
  /* Back */
  .mascot-area {
    position: absolute; right: -110px; top: -70px;
    width: 430px; height: 430px; border-radius: 50%;
    background: radial-gradient(circle at 40% 55%, var(--blue-soft), #eef6fc 70%);
  }
  .person {
    position: absolute; left: 40px; top: 110px;
    border-left: 5px solid var(--blue); padding-left: 18px;
  }
  .person__name { font-size: 30px; font-weight: 500; color: var(--blue); line-height: 1.1; }
  .person__role { font-size: 18px; font-weight: 500; color: var(--orange); margin-top: 4px; }
  .contact {
    position: absolute; left: 63px; top: 232px;
    font-size: 17px; color: var(--ink); line-height: 1.45; letter-spacing: 0.5px;
  }
  .contact__address { margin-bottom: 2px; }
  .contact__row { display: flex; align-items: center; gap: 10px; }
  .contact__icon { width: 15px; height: 15px; flex: none; }
</style>
</head>
<body>
<main class="sheet">
  <section class="card card--front" aria-label="Card front">
    <div class="brand">
      <span class="brand__dot"></span>
      <span class="brand__name">Tall Pine Computing</span>
    </div>
    <p class="tagline">Rooted in technology</p>
  </section>

  <section class="card card--back" aria-label="Card back">
    <div class="mascot-area" role="img" aria-label="Large brand mascot decoration"></div>
    <div class="person">
      <p class="person__name">Jordan Reyes</p>
      <p class="person__role">CEO/Founder</p>
    </div>
    <div class="contact">
      <p class="contact__address">218 Harbor View Lane<br>Seaview, Maine 04321</p>
      <p class="contact__row">
        <svg class="contact__icon" viewBox="0 0 16 16" aria-hidden="true"><path fill="#1a8fd6" d="M3.5 1.5l2.5 0 1 3.5-1.6 1.2a8 8 0 0 0 4.4 4.4L11 9l3.5 1v2.5c0 .8-.7 1.5-1.5 1.5A11.5 11.5 0 0 1 2 3c0-.8.7-1.5 1.5-1.5z"/></svg>
        555 014 2290
      </p>
      <p class="contact__row">
        <svg class="contact__icon" viewBox="0 0 16 16" aria-hidden="true"><rect x="1" y="3" width="14" height="10" rx="1.5" fill="#1a8fd6"/><path d="M2 4.5l6 4.5 6-4.5" fill="none" stroke="#fff" stroke-width="1.3"/></svg>
        mail@tallpinecomputing.com
      </p>
      <p class="contact__row">
        <svg class="contact__icon" viewBox="0 0 16 16" aria-hidden="true"><circle cx="8" cy="8" r="7" fill="#1a8fd6"/><path d="M1.5 8h13M8 1.2c-2.5 2.5-2.5 11.1 0 13.6M8 1.2c2.5 2.5 2.5 11.1 0 13.6" fill="none" stroke="#fff" stroke-width="1"/></svg>
        www.tallpinecomputing.com
      </p>
    </div>
  </section>
</main>
</body>
</html>
```